Modern corporate presentation

We need a clean, restrained company presentation in a modern Prezi style (design templates are attached for orientation). Please see the attachment for the briefing, colors and our corporate design.

content 1
Title:

FILOVAN
We connect worlds.
Digitization = increase in customer satisfaction

content 2
Animated on photo of company building (photo attached)

Text:

As Europe's leading service provider for business process outsourcing, we optimize your document management along the entire process chain of your document cycles, including physical long-term archiving after processing - efficiently, flexibly, individually and transparently!

content 3
Title: History
Overview of history as a timeline (see example design template slide 2) with dates and icons
Text:
1995
1997
2000
2016
2018
2021

content 4 or onwards
Morph transitions / individual seasons
1995 Founded by Lothar Brenner
1997 Start of ARKI@NET development
2000 real start ARKI@NET, certification GoB/S and KVR
2016 Development of Big Data + inMemory searches, first processes with AI
2018
ARKI@NET goes mobile
Expansion of the Lindtal site with a new logistics center
Launch Papyrix concept
2021 More than 400 satisfied employees

content 5
Title: Facts and Figures
Animated to morph the following texts/numbers:

family business
400 employees at different locations
Own data centers
7,500 pallet spaces
50,000 active users daily on the ARKI@NET platform
525 000 receipts per month
210 customers from all over Europe
all necessary certifications

content 6
Title: Product and service portfolio
Combine yourself...
Create animation from Lego building blocks, which are put together, morph individually according to the order (1-3).

Module 1:
system platform
• Audit-proof archiving ARKI@NET
• Fully integrated document management
• Complete, certified KVR® integration

Module 2:
solution modules
• Digital files
• Invoice receipt workflow
ordering system
• Digital inbox
• Case management
• Data Lantern

Module 3:

process services
• Storage
• Scanning Service
• Collection Services
• BPO Inbox
• BPO invoice receipt

content 7
Title: Good Reasons / Benefits
Trust / full-service provider for document-based business processes completely own solution
Portfolio / depiction of the entire process chain from a single source
Experience / reference projects of all sizes and industries
Employees / All services are provided by our own staff without the involvement of subcontractors

content 8
Title: The 100% Philosophy

Overview of the following 3 main points, which are highlighted individually below:

The system
Services
Privacy and Certifications
___

The system
• 100% own data center with 24x7 operation, incl. backup data center
• Certified KVR partner
• Real, completely in-house developed SaaS solution for data center operations only
• Maintenance, support and updates included
• Web-based application

Services
• Combination of man & machine
• Service level agreements, service defined in terms of time
• Penalty for non-fulfilment

Privacy and certifications:
• All common certifications
• Own compliance management
• Data protection according to GDPR

Font styles to use
Other font styles liked:
• Myrlad Pro Bold für Head und Sublines, Lucida Grande Regular für Fließtexte

Requirements
Must have
• clean and reserved, taking our corporate design into account
Nice to have
• Prezi Style, seamless transitions (similar to a scrollipage)

```html
<!DOCTYPE html>
<html lang="de">
<head>
<meta charset="utf-8">
<title>FILOVAN – Unternehmenspräsentation Übersicht</title>
<link href="https://fonts.googleapis.com/css2?family=Raleway:wght@100;200&family=Source+Sans+3:wght@300;400;600;700&display=swap" rel="stylesheet">
<style>
:root{
  --canvas:#4b4b4b;
  --navy:#27323e;
  --gold:#b9aa84;
  --blue:#6d8ca6;
  --grey:#8f8f8f;
  --ink:#333538;
  --paper:#f5f5f5;
  --white:#ffffff;
  --faint:#e3e3e3;
  --mute:#9b9b9b;
}
*{box-sizing:border-box;margin:0;padding:0}
html,body{width:1200px;height:960px;overflow:hidden;background:var(--canvas)}
body{position:relative;font-family:"Source Sans 3",sans-serif;color:var(--ink)}
.slide{position:absolute;width:182px;height:102px;overflow:hidden;background:var(--paper)}
.c1{left:26px}.c2{left:219px}.c3{left:413px}.c4{left:607px}.c5{left:800px}.c6{left:994px}
.r1{top:34px}.r2{top:148px}.r3{top:262px}.r4{top:376px}.r5{top:490px}.r6{top:603px}.r7{top:717px}.r8{top:832px}
.abs{position:absolute}

.photo{position:absolute;inset:0}
.photo.dark{background:linear-gradient(180deg,#45494c 0%,#2e3033 55%,#1f2123 100%)}
.photo.light{background:linear-gradient(180deg,#e6e7e8 0%,#f1f1f1 45%,#cfd2d4 100%)}
.photo.blue{background:linear-gradient(180deg,#8aa1b4 0%,#6d8ca6 55%,#5a7890 100%)}
.photo.sky{background:linear-gradient(180deg,#9fb7cc 0%,#d9e2ea 50%,#55687a 100%)}

.mark{display:flex;align-items:center;gap:1.5px;font-weight:400;letter-spacing:.2px}
.mark i{display:block;background:currentColor}
.mark.lg{font-size:8px;color:var(--white)}
.mark.lg i{width:5px;height:4px}
.mark.sm{font-size:2.6px;color:var(--ink)}
.mark.sm i{width:2px;height:1.6px}

.t-logo{position:absolute;left:26px;top:26px}
.claim{position:absolute;left:26px;top:70px;font-size:4.3px;font-weight:700;letter-spacing:.3px;color:var(--white)}
.subclaim{position:absolute;left:26px;top:76px;font-size:2.4px;color:#ddd}
.date{position:absolute;left:160px;top:86px;font-size:2.2px;color:#eee}
.title-light .claim{color:var(--ink)}.title-light .subclaim,.title-light .date{color:#666}
.title-light .mark.lg{color:var(--ink)}
.title-blue .claim{color:var(--gold)}
.title-blue .date{border:.3px solid #eee;padding:.3px 1.5px;top:85px}

.quote-panel{position:absolute;left:0;top:0;width:101px;height:102px;background:var(--white)}
.quote-mark{position:absolute;left:19px;top:22px;font-family:Raleway,sans-serif;font-weight:200;font-size:14px;color:var(--ink)}
.quote-text{position:absolute;left:19px;top:47px;width:58px;font-size:2.4px;line-height:3.3px;color:#555}
.quote-photo{left:101px;right:0;top:0;bottom:0}
.quote-logo{position:absolute;left:19px;top:91px}
.quote-foot{position:absolute;left:130px;top:92px;font-size:2.2px;color:#fff;letter-spacing:.2px}

.arch{position:absolute;left:-16px;right:-16px;top:6px;bottom:-30px;background:var(--paper);border-radius:50% 50% 0 0/45% 45% 0 0}
.menu-logo{position:absolute;left:0;right:0;top:26px;display:flex;justify-content:center}
.menu-logo .mark.lg{color:var(--ink)}
.pill{position:absolute;width:37px;height:16px;border-radius:8px;color:var(--white);font-size:2.3px;font-weight:700;display:flex;align-items:center;justify-content:center;text-align:center;line-height:2.8px;padding:0 3px}

.sec-photo{position:absolute;inset:0;background:linear-gradient(180deg,#e8e9ea,#f4f4f4 60%,#dcdedf)}
.sec-panel{position:absolute}
.sec-panel.inset{left:9px;top:17px;right:0;bottom:0}
.sec-panel.flush{left:0;top:0;width:174px;height:85px}
.sec-num{position:absolute;font-family:Raleway,sans-serif;font-weight:100;font-size:38px;line-height:1;color:transparent;-webkit-text-stroke:.6px var(--white)}
.sec-title{position:absolute;font-size:8px;font-weight:600;color:var(--white);line-height:7.6px}

.head{position:absolute;left:0;right:0;top:0;height:17px;line-height:17px;text-align:center;font-size:5.6px;font-weight:600;color:var(--white)}
.card{position:absolute;left:9px;top:17px;right:0;bottom:0;background:var(--paper)}
.foot{position:absolute;left:20px;right:12px;bottom:3px;border-top:.3px solid #ddd;padding-top:1px;display:flex;justify-content:space-between;align-items:center;font-size:2px;color:#999}
.foot b{font-weight:400;color:#555;border-left:.3px solid #999;padding-left:1.5px;margin-left:1.5px}
.bg-navy{background:var(--navy)}.bg-gold{background:var(--gold)}.bg-blue{background:var(--blue)}.bg-grey{background:var(--grey)}.bg-dark{background:#363738}

.timeline{position:absolute;left:24px;top:50px;display:flex;align-items:center;gap:1px}
.chev{width:22px;height:5px;font-size:2.4px;font-weight:700;color:var(--white);display:flex;align-items:center;justify-content:center;clip-path:polygon(0 0,86% 0,100% 50%,86% 100%,0 100%,12% 50%)}
.chev.on{width:30px;height:8px;font-size:4px}
.y95{background:#cbbd99}.y97{background:#35373a}.y00{background:#8d8d8d}.y16{background:#7a7d80}.y18{background:#e7e7e7;color:#555}.y21{background:var(--blue)}
.chev.off{background:#ebebeb;color:#c4c4c4}
.ev{position:absolute;display:flex;align-items:center;gap:2.5px;font-size:2.8px;line-height:3.4px;color:#444}
.ev .ic{flex:none;width:9px;height:9px;border:.4px solid #aaa;border-radius:50%;display:flex;align-items:center;justify-content:center;color:#777}
.ev .ic svg{width:5px;height:5px}
.ev.faint{opacity:.3}
.ev.mini{font-size:1.9px;line-height:2.4px;gap:1.5px}
.ev.mini .ic{width:6px;height:6px}
.ev.mini .ic svg{width:3.4px;height:3.4px}

.fact-card{position:absolute;left:0;top:0;width:174px;height:85px;background:var(--paper)}
.band{position:absolute;left:0;width:174px;top:85px;height:17px;line-height:17px;text-align:center;font-size:5.2px;color:var(--white);font-weight:400}
.strip-label{position:absolute;right:2px;top:6px;font-size:1.8px;color:rgba(255,255,255,.8);writing-mode:vertical-rl;letter-spacing:.2px}
.icongrid{position:absolute;left:130px;top:14px;display:grid;grid-template-columns:10px 10px;column-gap:10px;row-gap:6px;color:var(--gold)}
.icongrid svg{width:10px;height:10px;opacity:.45}
.icongrid svg.hi{opacity:1;transform:scale(1.35)}
.divider{position:absolute;left:115px;top:12px;width:.3px;height:66px;background:#ddd}
.fact{position:absolute;left:33px;top:22px;color:var(--gold)}
.fact svg{width:12px;height:12px}
.fact .num{font-size:8px;font-weight:300;line-height:8px;margin-top:2px}
.fact .lbl{font-size:4.2px;color:#333;line-height:4.4px}
.fact .sub{font-size:1.9px;color:#aaa}

.blocks{position:absolute;background:linear-gradient(180deg,#c8cacc 0%,#c8cacc 32%,#3d4148 33%,#3d4148 66%,#7d99b2 67%,#7d99b2 100%);border-radius:1px}
.plabel{position:absolute;font-size:3.2px;font-weight:600;color:#333;display:flex;align-items:center;gap:2px}
.plabel i{width:6px;height:6px;border:.3px solid #aaa;border-radius:50%;display:block}
.orb{position:absolute;left:18px;top:32px;width:46px;height:46px;border-radius:50%;background:#ececec;border:.4px solid #ccc}
.orb .blocks{left:11px;top:14px;width:24px;height:16px}
.pbox{position:absolute;left:106px;top:26px;width:60px;height:52px;background:var(--white);padding:4px 5px}
.pbox h3{font-size:4px;font-weight:400;margin-bottom:3px}
.pbox ul{list-style:none}
.pbox li{font-size:2.3px;line-height:2.8px;color:#555;padding-left:2.5px;position:relative}
.pbox li::before{content:"";position:absolute;left:0;top:1px;width:1px;height:1px;border-radius:50%;background:#888}
.picon{position:absolute;left:89px;top:38px;width:11px;height:11px;color:var(--gold)}
.dots{position:absolute;left:34px;top:82px;display:flex;gap:1px}
.dots i{width:2.6px;height:2.6px;border-radius:50%;border:.3px solid var(--blue);display:block}
.dots i.on{background:var(--blue)}

.arcs{position:absolute;left:0;top:0;width:174px;height:85px}
.rtext{position:absolute;font-size:1.9px;line-height:2.4px;color:#777;text-align:center;width:30px}
.ricon{position:absolute;width:8px;height:8px;color:#888}

.plist{position:absolute;left:46px;top:37px}
.plist li{list-style:none;display:flex;align-items:center;gap:4px;font-size:3px;color:#555;height:14.5px}
.plist i,.picol i{display:flex;align-items:center;justify-content:center;width:8px;height:8px;border:.4px solid #ccc;border-radius:50%;color:#aaa}
.picol{position:absolute;left:27px;top:35px;display:flex;flex-direction:column;gap:9px}
.picol i.on{background:var(--gold);border-color:var(--gold);color:#fff;width:9px;height:9px}
.picol svg{width:5px;height:5px}
.phtitle{position:absolute;left:55px;top:36px;font-size:4.2px;color:var(--blue);line-height:4.4px}
.phicon{position:absolute;left:57px;top:46px;width:12px;height:12px;color:var(--gold)}
.phbox{position:absolute;left:102px;top:28px;width:69px;height:56px;background:var(--paper);padding:4px 4px}
.phbox li{list-style:none;font-size:2.2px;line-height:2.7px;color:#555;padding-left:2.5px;position:relative;margin-bottom:1px}
.phbox li::before{content:"";position:absolute;left:0;top:1px;width:1px;height:1px;border-radius:50%;background:#777}
.ph-card{background:var(--white)}

.thx-word{position:absolute;font-size:6px;color:var(--white)}
.contact{position:absolute;top:74px;display:flex;gap:6px;align-items:flex-start;font-size:1.9px;line-height:2.5px;color:#ccc}
.contact .vl{width:.3px;height:9px;background:#888}
.social{position:absolute;left:141px;top:93px;display:flex;gap:1px}
.social i{width:3px;height:3px;border-radius:50%;background:#fff;display:block}
.web{position:absolute;left:160px;top:93px;font-size:2px;color:#ccc;border-left:.3px solid #888;padding-left:2px}
</style>
</head>
<body>

<svg width="0" height="0" style="position:absolute" aria-hidden="true">
  <defs>
    <symbol id="i-building" viewBox="0 0 16 16"><g fill="none" stroke="currentColor" stroke-width="0.8"><rect x="4" y="2" width="8" height="12"/><path d="M6 4h1M9 4h1M6 6.5h1M9 6.5h1M6 9h1M9 9h1M7 14v-2.5h2V14"/></g></symbol>
    <symbol id="i-star" viewBox="0 0 16 16"><path fill="none" stroke="currentColor" stroke-width="0.8" d="M8 2l1.8 3.8 4.1.5-3 2.8.8 4.1L8 11.2 4.3 13.2l.8-4.1-3-2.8 4.1-.5z"/></symbol>
    <symbol id="i-people" viewBox="0 0 16 16"><g fill="none" stroke="currentColor" stroke-width="0.8"><circle cx="5" cy="6" r="1.6"/><circle cx="11" cy="6" r="1.6"/><circle cx="8" cy="4.5" r="1.8"/><path d="M2 12c0-2 1.4-3.5 3-3.5M14 12c0-2-1.4-3.5-3-3.5M4.5 13c0-2.5 1.6-4.3 3.5-4.3s3.5 1.8 3.5 4.3"/></g></symbol>
    <symbol id="i-person" viewBox="0 0 16 16"><g fill="none" stroke="currentColor" stroke-width="0.8"><circle cx="8" cy="5" r="2.3"/><path d="M3.5 14c0-3 2-5 4.5-5s4.5 2 4.5 5"/></g></symbol>
    <symbol id="i-gear" viewBox="0 0 16 16"><g fill="none" stroke="currentColor" stroke-width="0.8"><circle cx="8" cy="8" r="2.2"/><circle cx="8" cy="8" r="5" stroke-dasharray="2 1.3"/></g></symbol>
    <symbol id="i-inbox" viewBox="0 0 16 16"><g fill="none" stroke="currentColor" stroke-width="0.8"><path d="M2 9l2-4h8l2 4v4H2z M2 9h3.5l1 1.5h3l1-1.5H14"/><path d="M8 1.5v5M6.3 4.8L8 6.5l1.7-1.7"/></g></symbol>
    <symbol id="i-badge" viewBox="0 0 16 16"><g fill="none" stroke="currentColor" stroke-width="0.8"><circle cx="8" cy="7" r="4.6" stroke-dasharray="1.6 .8"/><path d="M8 4.6l.8 1.6 1.7.2-1.2 1.2.3 1.7L8 8.5l-1.6.8.3-1.7-1.2-1.2 1.7-.2z"/><path d="M5.5 11l-1 3.5 2-1 1.5 1.5M10.5 11l1 3.5-2-1-1.5 1.5"/></g></symbol>
    <symbol id="i-power" viewBox="0 0 16 16"><g fill="none" stroke="currentColor" stroke-width="0.9"><path d="M5 4.5a5 5 0 1 0 6 0"/><path d="M8 2.5v5"/></g></symbol>
    <symbol id="i-hourglass" viewBox="0 0 16 16"><path fill="none" stroke="currentColor" stroke-width="0.9" d="M4.5 2h7M4.5 14h7M5.5 2c0 3 5 4 5 6s-5 3-5 6M10.5 2c0 3-5 4-5 6s5 3 5 6"/></symbol>
    <symbol id="i-bolt" viewBox="0 0 16 16"><path fill="none" stroke="currentColor" stroke-width="0.9" d="M9 1.5L4 9h4l-1 5.5L12 7H8z"/></symbol>
    <symbol id="i-layers" viewBox="0 0 16 16"><g fill="none" stroke="currentColor" stroke-width="0.9"><path d="M8 3l5 2.5-5 2.5-5-2.5z"/><path d="M3 8l5 2.5L13 8M3 10.5L8 13l5-2.5"/></g></symbol>
    <symbol id="i-truck" viewBox="0 0 16 16"><g fill="none" stroke="currentColor" stroke-width="0.9"><path d="M1.5 5h8v6h-8zM9.5 7h3l2 2v2h-5"/><circle cx="4.5" cy="12" r="1.2"/><circle cx="11.5" cy="12" r="1.2"/></g></symbol>
    <symbol id="i-house" viewBox="0 0 16 16"><g fill="none" stroke="currentColor" stroke-width="0.8"><path d="M3 7.5L8 3l5 4.5V14H3z"/><path d="M6.5 14v-3.5h3V14"/></g></symbol>
    <symbol id="i-cube" viewBox="0 0 16 16"><g fill="none" stroke="currentColor" stroke-width="0.8"><path d="M8 2l5.5 3v6L8 14l-5.5-3V5z M2.5 5L8 8l5.5-3M8 8v6"/></g></symbol>
    <symbol id="i-hands" viewBox="0 0 16 16"><g fill="none" stroke="currentColor" stroke-width="0.8"><path d="M1.5 8l3-3 3 1.5 2-1 5 3-3 3.5-2-1-2 1.5z M7.5 6.5l-2 2.5"/></g></symbol>
    <symbol id="i-shield" viewBox="0 0 16 16"><g fill="none" stroke="currentColor" stroke-width="0.8"><path d="M8 2l5 2v4c0 3-2.5 5-5 6-2.5-1-5-3-5-6V4z"/><path d="M5.8 8l1.6 1.6 3-3"/></g></symbol>
    <symbol id="i-puzzle" viewBox="0 0 16 16"><g fill="none" stroke="currentColor" stroke-width="0.8"><path d="M3 3h4v1.5a1.2 1.2 0 1 0 2 0V3h4v4h-1.5a1.2 1.2 0 1 0 0 2H13v4H3z"/></g></symbol>
  </defs>
</svg>

<!-- ROW 1 -->
<section class="slide c1 r1 title-dark">
  <div class="photo dark" role="img" aria-label="Company headquarters building beside a lake, dark toned"></div>
  <div class="t-logo"><span class="mark lg"><i></i>FILOVAN</span></div>
  <div class="claim">WIR VERBINDEN WELTEN</div>
  <div class="subclaim">Digitalisierung = Steigerung der Kundenzufriedenheit</div>
  <div class="date">APR 2023</div>
</section>

<section class="slide c2 r1 title-light">
  <div class="photo light" role="img" aria-label="Company headquarters building beside a lake, light toned"></div>
  <div class="t-logo"><span class="mark lg"><i></i>FILOVAN</span></div>
  <div class="claim">WIR VERBINDEN WELTEN</div>
  <div class="subclaim">Digitalisierung = Steigerung der Kundenzufriedenheit</div>
  <div class="date">APR 2023</div>
</section>

<section class="slide c3 r1 title-blue">
  <div class="photo blue" role="img" aria-label="Company headquarters building beside a lake, blue toned"></div>
  <div class="t-logo"><span class="mark lg"><i></i>FILOVAN</span></div>
  <div class="claim">WIR VERBINDEN WELTEN</div>
  <div class="subclaim">Digitalisierung = Steigerung der Kundenzufriedenheit</div>
  <div class="date">APR 2023</div>
</section>

<section class="slide c4 r1">
  <div class="quote-panel"></div>
  <div class="abs quote-photo photo sky" role="img" aria-label="Company building reflected in a lake under a blue sky"></div>
  <div class="quote-mark">99</div>
  <p class="quote-text">Als europaweit führender Dienstleister für Business Process Outsourcing optimieren wir Ihr Dokumentenmanagement entlang der gesamten Prozesskette Ihrer Dokumentenkreisläufe inkl. der physischen Langzeitarchivierung nach der Verarbeitung – effizient, flexibel, individuell und transparent!</p>
  <div class="quote-logo"><span class="mark sm"><i></i>FILOVAN</span></div>
  <div class="quote-foot">PRESENTATION TITLE &nbsp;|&nbsp; 01</div>
</section>

<section class="slide c5 r1">
  <div class="photo sky" role="img" aria-label="Company building rising above a white arch, lake in the background"></div>
  <div class="arch"></div>
  <div class="menu-logo"><span class="mark lg"><i></i>FILOVAN</span></div>
  <div class="pill bg-navy" style="left:33px;top:47px">HISTORIE</div>
  <div class="pill bg-gold" style="left:73px;top:47px">ZAHLEN UND FAKTEN</div>
  <div class="pill bg-blue" style="left:113px;top:47px">PRODUKT UND LEISTUNGSPORTFOLIO</div>
  <div class="pill bg-grey" style="left:53px;top:69px">GUTE GRÜNDE / VORTEILE</div>
  <div class="pill bg-navy" style="left:93px;top:69px">DIE 100% PHILOSOPHIE</div>
</section>

<!-- ROW 2 -->
<section class="slide c1 r2">
  <div class="sec-photo" role="img" aria-label="Company building, faded background"></div>
  <div class="sec-panel inset bg-navy"></div>
  <div class="sec-num" style="left:22px;top:52px">02</div>
  <div class="sec-title" style="left:77px;top:69px">Historie.</div>
</section>

<section class="slide c2 r2 bg-navy">
  <div class="head">Historie</div><div class="card"></div>
  <div class="timeline">
    <span class="chev y95">1995</span><span class="chev y97">1997</span><span class="chev y00">2000</span><span class="chev y16">2016</span><span class="chev y18">2018</span><span class="chev y21">2021</span>
  </div>
  <div class="foot"><span class="mark sm"><i></i>FILOVAN</span><span>PRESENTATION TITLE<b>02</b></span></div>
</section>

<section class="slide c3 r2 bg-navy">
  <div class="head">Historie</div><div class="card"></div>
  <div class="timeline">
    <span class="chev on y95">1995</span><span class="chev off">1997</span><span class="chev off">2000</span><span class="chev off">2016</span><span class="chev off">2018</span><span class="chev off">2021</span>
  </div>
  <div class="ev" style="left:31px;top:62px"><span class="ic"><svg><use href="#i-power"/></svg></span><p>Gegründet von<br>Lothar Brenner</p></div>
  <div class="foot"><span class="mark sm"><i></i>FILOVAN</span><span>PRESENTATION TITLE<b>02</b></span></div>
</section>

<section class="slide c4 r2 bg-navy">
  <div class="head">Historie</div><div class="card"></div>
  <div class="timeline">
    <span class="chev off">1995</span><span class="chev on y97">1997</span><span class="chev off">2000</span><span class="chev off">2016</span><span class="chev off">2018</span><span class="chev off">2021</span>
  </div>
  <div class="ev" style="left:53px;top:30px"><span class="ic"><svg><use href="#i-hourglass"/></svg></span><p>Start Entwicklung<br>ARKI@NET</p></div>
  <div class="ev mini faint" style="left:31px;top:60px"><span class="ic"><svg><use href="#i-power"/></svg></span><p>Gegründet von<br>Lothar Brenner</p></div>
  <div class="foot"><span class="mark sm"><i></i>FILOVAN</span><span>PRESENTATION TITLE<b>02</b></span></div>
</section>

<section class="slide c5 r2 bg-navy">
  <div class="head">Historie</div><div class="card"></div>
  <div class="timeline">
    <span class="chev off">1995</span><span class="chev off">1997</span><span class="chev on y00">2000</span><span class="chev off">2016</span><span class="chev off">2018</span><span class="chev off">2021</span>
  </div>
  <div class="ev mini faint" style="left:33px;top:36px"><span class="ic"><svg><use href="#i-hourglass"/></svg></span><p>Start Entwicklung<br>ARKI@NET</p></div>
  <div class="ev mini faint" style="left:31px;top:62px"><span class="ic"><svg><use href="#i-power"/></svg></span><p>Gegründet von<br>Lothar Brenner</p></div>
  <div class="ev" style="left:64px;top:62px"><span class="ic"><svg><use href="#i-bolt"/></svg></span><p>Echtstart ARKI@NET,<br>Zertifizierung GoB/S<br>und KVR</p></div>
  <div class="foot"><span class="mark sm"><i></i>FILOVAN</span><span>PRESENTATION TITLE<b>02</b></span></div>
</section>

<!-- ROW 3 -->
<section class="slide c2 r3 bg-navy">
  <div class="head">Historie</div><div class="card"></div>
  <div class="timeline">
    <span class="chev off">1995</span><span class="chev off">1997</span><span class="chev off">2000</span><span class="chev on y16">2016</span><span class="chev off">2018</span><span class="chev off">2021</span>
  </div>
  <div class="ev mini faint" style="left:30px;top:38px"><span class="ic"><svg><use href="#i-hourglass"/></svg></span><p>Start Entwicklung<br>ARKI@NET</p></div>
  <div class="ev mini faint" style="left:28px;top:62px"><span class="ic"><svg><use href="#i-power"/></svg></span><p>Gegründet von<br>Lothar Brenner</p></div>
  <div class="ev mini faint" style="left:56px;top:62px"><span class="ic"><svg><use href="#i-bolt"/></svg></span><p>Echtstart ARKI@NET,<br>Zertifizierung GoB/S</p></div>
  <div class="ev" style="left:92px;top:28px"><span class="ic"><svg><use href="#i-layers"/></svg></span><p>Entwicklung Big Data +<br>inMemory Suchen, Erste<br>Prozesse mit KI</p></div>
  <div class="foot"><span class="mark sm"><i></i>FILOVAN</span><span>PRESENTATION TITLE<b>02</b></span></div>
</section>

<section class="slide c3 r3 bg-navy">
  <div class="head">Historie</div><div class="card"></div>
  <div class="timeline">
    <span class="chev off">1995</span><span class="chev off">1997</span><span class="chev off">2000</span><span class="chev off">2016</span><span class="chev on y18">2018</span><span class="chev off">2021</span>
  </div>
  <div class="ev mini faint" style="left:26px;top:36px"><span class="ic"><svg><use href="#i-hourglass"/></svg></span><p>Start Entwicklung<br>ARKI@NET</p></div>
  <div class="ev mini faint" style="left:58px;top:36px"><span class="ic"><svg><use href="#i-layers"/></svg></span><p>Big Data +<br>inMemory Suchen</p></div>
  <div class="ev mini faint" style="left:26px;top:62px"><span class="ic"><svg><use href="#i-power"/></svg></span><p>Gegründet von<br>Lothar Brenner</p></div>
  <div class="ev mini faint" style="left:56px;top:62px"><span class="ic"><svg><use href="#i-bolt"/></svg></span><p>Echtstart ARKI@NET,<br>Zertifizierung GoB/S</p></div>
  <div class="ev" style="left:95px;top:62px"><span class="ic"><svg><use href="#i-truck"/></svg></span><p>ARKI@NET wird mobil,<br>Erweiterung des Standortes<br>Lindtal durch neues<br>Logistikzentrum;<br>Start Papyrix Konzept</p></div>
  <div class="foot"><span class="mark sm"><i></i>FILOVAN</span><span>PRESENTATION TITLE<b>02</b></span></div>
</section>

<section class="slide c4 r3 bg-navy">
  <div class="head">Historie</div><div class="card"></div>
  <div class="timeline">
    <span class="chev off">1995</span><span class="chev off">1997</span><span class="chev off">2000</span><span class="chev off">2016</span><span class="chev off">2018</span><span class="chev on y21">2021</span>
  </div>
  <div class="ev mini faint" style="left:26px;top:36px"><span class="ic"><svg><use href="#i-hourglass"/></svg></span><p>Start Entwicklung<br>ARKI@NET</p></div>
  <div class="ev mini faint" style="left:56px;top:36px"><span class="ic"><svg><use href="#i-layers"/></svg></span><p>Big Data +<br>inMemory Suchen</p></div>
  <div class="ev mini faint" style="left:26px;top:62px"><span class="ic"><svg><use href="#i-power"/></svg></span><p>Gegründet von<br>Lothar Brenner</p></div>
  <div class="ev mini faint" style="left:56px;top:62px"><span class="ic"><svg><use href="#i-bolt"/></svg></span><p>Echtstart ARKI@NET,<br>Zertifizierung GoB/S</p></div>
  <div class="ev mini faint" style="left:92px;top:62px"><span class="ic"><svg><use href="#i-truck"/></svg></span><p>ARKI@NET wird mobil,<br>neues Logistikzentrum</p></div>
  <div class="ev" style="left:107px;top:28px"><span class="ic"><svg><use href="#i-people"/></svg></span><p>Mehr als 400<br>zufriedene<br>Mitarbeiter</p></div>
  <div class="foot"><span class="mark sm"><i></i>FILOVAN</span><span>PRESENTATION TITLE<b>02</b></span></div>
</section>

<section class="slide c5 r3 bg-navy">
  <div class="head">Historie</div><div class="card"></div>
  <div class="timeline">
    <span class="chev y95">1995</span><span class="chev y97">1997</span><span class="chev y00">2000</span><span class="chev y16">2016</span><span class="chev y18">2018</span><span class="chev y21">2021</span>
  </div>
  <div class="ev mini" style="left:31px;top:38px"><p>Start Entwicklung<br>ARKI@NET</p><span class="ic"><svg><use href="#i-hourglass"/></svg></span></div>
  <div class="ev mini" style="left:75px;top:37px"><p>Entwicklung Big Data +<br>inMemory Suchen,<br>Erste Prozesse mit KI</p><span class="ic"><svg><use href="#i-layers"/></svg></span></div>
  <div class="ev mini" style="left:122px;top:38px"><p>Mehr als 400<br>zufriedene Mitarbeiter</p><span class="ic"><svg><use href="#i-people"/></svg></span></div>
  <div class="ev mini" style="left:25px;top:62px"><span class="ic"><svg><use href="#i-power"/></svg></span><p>Gegründet von<br>Lothar Brenner</p></div>
  <div class="ev mini" style="left:64px;top:62px"><span class="ic"><svg><use href="#i-bolt"/></svg></span><p>Echtstart ARKI@NET,<br>Zertifizierung GoB/S<br>und KVR</p></div>
  <div class="ev mini" style="left:106px;top:62px"><span class="ic"><svg><use href="#i-truck"/></svg></span><p>ARKI@NET wird mobil,<br>Erweiterung des Standortes<br>durch neues Logistikzentrum,<br>Start Papyrix Konzept</p></div>
  <div class="foot"><span class="mark sm"><i></i>FILOVAN</span><span>PRESENTATION TITLE<b>02</b></span></div>
</section>

<!-- ROW 4 -->
<section class="slide c1 r4">
  <div class="sec-photo" role="img" aria-label="Company building, faded background"></div>
  <div class="sec-panel flush bg-gold"></div>
  <div class="sec-num" style="left:13px;top:11px">03</div>
  <div class="sec-title" style="left:69px;top:27px">Zahlen und Facten.</div>
</section>

<section class="slide c2 r4 bg-gold">
  <div class="fact-card"></div>
  <div class="icongrid">
    <svg><use href="#i-building"/></svg><svg><use href="#i-star"/></svg>
    <svg><use href="#i-people"/></svg><svg><use href="#i-person"/></svg>
    <svg><use href="#i-gear"/></svg><svg><use href="#i-inbox"/></svg>
    <svg><use href="#i-people"/></svg><svg><use href="#i-badge"/></svg>
  </div>
  <div class="band">Zahlen und Facten</div>
  <div class="strip-label">FILOVAN · 03</div>
</section>

<section class="slide c3 r4 bg-gold">
  <div class="fact-card"></div>
  <div class="divider"></div>
  <div class="fact" style="top:22px"><svg><use href="#i-building"/></svg><div class="lbl" style="margin-top:3px">Familienunternehmen</div></div>
  <div class="icongrid">
    <svg class="hi"><use href="#i-building"/></svg><svg><use href="#i-star"/></svg>
    <svg><use href="#i-people"/></svg><svg><use href="#i-person"/></svg>
    <svg><use href="#i-gear"/></svg><svg><use href="#i-inbox"/></svg>
    <svg><use href="#i-people"/></svg><svg><use href="#i-badge"/></svg>
  </div>
  <div class="band">Zahlen und Facten</div>
  <div class="strip-label">FILOVAN · 03</div>
</section>

<section class="slide c4 r4 bg-gold">
  <div class="fact-card"></div>
  <div class="divider"></div>
  <div class="fact" style="top:22px;left:34px"><svg><use href="#i-people"/></svg><div class="num">50,000</div><div class="lbl">aktive User täglich</div><div class="sub">auf der ARKI@NET Plattform</div></div>
  <div class="icongrid">
    <svg><use href="#i-building"/></svg><svg><use href="#i-star"/></svg>
    <svg><use href="#i-people"/></svg><svg><use href="#i-person"/></svg>
    <svg><use href="#i-gear"/></svg><svg><use href="#i-inbox"/></svg>
    <svg class="hi"><use href="#i-people"/></svg><svg><use href="#i-badge"/></svg>
  </div>
  <div class="band">Zahlen und Facten</div>
  <div class="strip-label">FILOVAN · 03</div>
</section>

<section class="slide c5 r4 bg-gold">
  <div class="fact-card"></div>
  <div class="divider"></div>
  <div class="fact" style="top:22px;left:34px"><svg><use href="#i-inbox"/></svg><div class="num">525,000</div><div class="lbl">Belege pro Monat</div></div>
  <div class="icongrid">
    <svg><use href="#i-building"/></svg><svg><use href="#i-star"/></svg>
    <svg><use href="#i-people"/></svg><svg><use href="#i-person"/></svg>
    <svg><use href="#i-gear"/></svg><svg class="hi"><use href="#i-inbox"/></svg>
    <svg><use href="#i-people"/></svg><svg><use href="#i-badge"/></svg>
  </div>
  <div class="band">Zahlen und Facten</div>
  <div class="strip-label">FILOVAN · 03</div>
</section>

<section class="slide c6 r4 bg-gold">
  <div class="fact-card"></div>
  <div class="divider"></div>
  <div class="fact" style="top:22px;left:33px"><svg style="width:14px;height:14px"><use href="#i-badge"/></svg><div class="lbl" style="margin-top:2px">alle notwendigen<br>Zertifizierungen</div></div>
  <div class="icongrid">
    <svg><use href="#i-building"/></svg><svg><use href="#i-star"/></svg>
    <svg><use href="#i-people"/></svg><svg><use href="#i-person"/></svg>
    <svg><use href="#i-gear"/></svg><svg><use href="#i-inbox"/></svg>
    <svg><use href="#i-people"/></svg><svg class="hi"><use href="#i-badge"/></svg>
  </div>
  <div class="band">Zahlen und Facten</div>
  <div class="strip-label">FILOVAN · 03</div>
</section>

<!-- ROW 5 -->
<section class="slide c1 r5">
  <div class="sec-photo" role="img" aria-label="Company building, faded background"></div>
  <div class="sec-panel inset bg-blue"></div>
  <div class="sec-num" style="left:22px;top:52px">04</div>
  <div class="sec-title" style="left:79px;top:63px">Produkt und<br>Leistungsportfolio.</div>
</section>

<section class="slide c2 r5 bg-blue">
  <div class="head">Produkt und Leistungsportfolio</div><div class="card ph-card"></div>
  <svg class="abs" style="left:0;top:0" width="182" height="102" aria-hidden="true">
    <path d="M48 44 Q70 30 92 36" fill="none" stroke="#c9c9c9" stroke-width=".4"/>
    <path d="M92 36 Q116 30 138 44" fill="none" stroke="#c9c9c9" stroke-width=".4"/>
    <path d="M93 60 Q92 70 88 75" fill="none" stroke="var(--blue)" stroke-width=".4"/>
  </svg>
  <div class="blocks" role="img" aria-label="Three stacked building blocks in grey, dark and blue" style="left:80px;top:36px;width:26px;height:18px"></div>
  <div class="plabel" style="left:40px;top:43px;flex-direction:column;align-items:center"><i></i>Systemplattform</div>
  <div class="plabel" style="left:114px;top:43px;flex-direction:column;align-items:center"><i></i>Prozessdienstleistungen</div>
  <div class="plabel" style="left:76px;top:74px"><i></i>Lösungsmodule</div>
  <div class="foot"><span class="mark sm"><i></i>FILOVAN</span><span>PRESENTATION TITLE<b>04</b></span></div>
</section>

<section class="slide c3 r5 bg-blue">
  <div class="head">Produkt und Leistungsportfolio</div><div class="card ph-card"></div>
  <svg class="abs" style="left:0;top:0" width="182" height="102" aria-hidden="true"><path d="M47 35 L62 34 L106 32" fill="none" stroke="var(--gold)" stroke-width=".4"/><circle cx="47" cy="35" r=".8" fill="var(--gold)"/></svg>
  <div class="orb"><div class="blocks" role="img" aria-label="Single grey building block" style="background:#c8cacc"></div></div>
  <svg class="picon"><use href="#i-house"/></svg>
  <div class="pbox"><h3 style="color:var(--gold)">Systemplattform</h3><ul><li>Revisionssichere Archivierung ARKI@NET</li><li>Dokumentenmanagement voll integriert</li><li>Vollständige, zertifizierte KVR® Integration</li></ul></div>
  <div class="dots"><i class="on"></i><i></i><i></i></div>
  <div class="foot"><span class="mark sm"><i></i>FILOVAN</span><span>PRESENTATION TITLE<b>04</b></span></div>
</section>

<section class="slide c4 r5 bg-blue">
  <div class="head">Produkt und Leistungsportfolio</div><div class="card ph-card"></div>
  <svg class="abs" style="left:0;top:0" width="182" height="102" aria-hidden="true"><path d="M47 35 L106 32" fill="none" stroke="var(--blue)" stroke-width=".4"/><circle cx="47" cy="35" r=".8" fill="var(--blue)"/></svg>
  <div class="orb"><div class="blocks" role="img" aria-label="Grey and dark building blocks stacked" style="background:linear-gradient(180deg,#c8cacc 0 48%,#3d4148 50% 100%)"></div></div>
  <svg class="picon"><use href="#i-cube"/></svg>
  <div class="pbox"><h3 style="color:var(--blue)">Lösungsmodule</h3><ul><li>Digitale Akten</li><li>Rechnungseingangsworkflow Bestellsystem</li><li>Digitaler Posteingang</li><li>Vorgangsmanagement</li><li>Data Lantern</li></ul></div>
  <div class="dots"><i class="on"></i><i class="on"></i><i></i></div>
  <div class="foot"><span class="mark sm"><i></i>FILOVAN</span><span>PRESENTATION TITLE<b>04</b></span></div>
</section>

<section class="slide c5 r5 bg-blue">
  <div class="head">Produkt und Leistungsportfolio</div><div class="card ph-card"></div>
  <svg class="abs" style="left:0;top:0" width="182" height="102" aria-hidden="true"><path d="M47 35 L106 32" fill="none" stroke="var(--gold)" stroke-width=".4"/><circle cx="47" cy="35" r=".8" fill="var(--gold)"/></svg>
  <div class="orb"><div class="blocks" role="img" aria-label="Three stacked building blocks in grey, dark and blue"></div></div>
  <svg class="picon"><use href="#i-gear"/></svg>
  <div class="pbox"><h3 style="color:var(--gold)">Prozessdienstleistungen</h3><ul><li>Lagerung</li><li>Scandienstleistung</li><li>Erfassungsdienstleistungen</li><li>BPO Posteingang</li><li>BPO Rechnungseingang</li></ul></div>
  <div class="dots"><i class="on"></i><i class="on"></i><i class="on"></i></div>
  <div class="foot"><span class="mark sm"><i></i>FILOVAN</span><span>PRESENTATION TITLE<b>04</b></span></div>
</section>

<!-- ROW 6 -->
<section class="slide c1 r6">
  <div class="sec-photo" role="img" aria-label="Company building, faded background"></div>
  <div class="sec-panel flush bg-grey"></div>
  <div class="sec-num" style="left:13px;top:11px">05</div>
  <div class="sec-title" style="left:70px;top:27px">Gute Gründe / Vorteile.</div>
</section>

<section class="slide c2 r6 bg-grey">
  <div class="fact-card"></div>
  <svg class="arcs" viewBox="0 0 174 85" aria-hidden="true">
    <g fill="none" stroke-width="2.6">
      <path d="M27 43 A15 15 0 0 1 57 43" stroke="#d6cbb0"/>
      <path d="M57 43 A15 15 0 0 0 87 43" stroke="#35373a"/>
      <path d="M87 43 A15 15 0 0 1 117 43" stroke="#35373a"/>
      <path d="M117 43 A15 15 0 0 0 147 43" stroke="#b5b5b5"/>
    </g>
    <g fill="#ececec"><circle cx="42" cy="43" r="9"/><circle cx="72" cy="43" r="9"/><circle cx="102" cy="43" r="9"/><circle cx="132" cy="43" r="9"/></g>
    <g font-size="2.4" fill="#333" text-anchor="middle" font-family="Source Sans 3, sans-serif"><text x="42" y="44">Vertrauen</text><text x="72" y="44">Portfolio</text><text x="102" y="44">Erfahrung</text><text x="132" y="44">Mitarbeiter</text></g>
  </svg>
  <div class="band">Gute Gründe / Vorteile</div>
  <div class="strip-label">FILOVAN · 05</div>
</section>

<section class="slide c3 r6 bg-grey">
  <div class="fact-card"></div>
  <svg class="arcs" viewBox="0 0 174 85" aria-hidden="true">
    <g fill="none" stroke-width="2.6">
      <path d="M27 43 A17 17 0 0 1 61 43" stroke="#cbbd99"/>
      <path d="M72 46 A13 13 0 0 0 98 46" stroke="#e4e4e4"/>
      <path d="M98 46 A13 13 0 0 1 124 46" stroke="#e4e4e4"/>
      <path d="M124 46 A13 13 0 0 0 150 46" stroke="#e4e4e4"/>
    </g>
    <g font-size="2.6" fill="#333" text-anchor="middle" font-family="Source Sans 3, sans-serif"><text x="44" y="44" font-weight="600" font-size="3">Vertrauen</text></g>
    <g font-size="1.8" fill="#bbb" text-anchor="middle" font-family="Source Sans 3, sans-serif"><text x="85" y="47">Portfolio</text><text x="111" y="47">Erfahrung</text><text x="137" y="47">Mitarbeiter</text></g>
  </svg>
  <svg class="ricon" style="left:40px;top:11px"><use href="#i-house"/></svg>
  <p class="rtext" style="left:29px;top:55px">Full-Service Provider für dokumentenbasierte Geschäftsprozesse mit vollständig eigener Lösung</p>
  <div class="band">Gute Gründe / Vorteile</div>
  <div class="strip-label">FILOVAN · 05</div>
</section>

<section class="slide c4 r6 bg-grey">
  <div class="fact-card"></div>
  <svg class="arcs" viewBox="0 0 174 85" aria-hidden="true">
    <g fill="none" stroke-width="2.6">
      <path d="M26 43 A13 13 0 0 1 52 43" stroke="#e4e4e4"/>
      <path d="M55 43 A17 17 0 0 0 89 43" stroke="#35373a"/>
      <path d="M96 43 A13 13 0 0 1 122 43" stroke="#e4e4e4"/>
      <path d="M122 43 A13 13 0 0 0 148 43" stroke="#e4e4e4"/>
    </g>
    <g font-size="1.8" fill="#bbb" text-anchor="middle" font-family="Source Sans 3, sans-serif"><text x="39" y="44">Vertrauen</text><text x="109" y="44">Erfahrung</text><text x="135" y="44">Mitarbeiter</text></g>
    <text x="72" y="44" font-size="3" font-weight="600" fill="#333" text-anchor="middle" font-family="Source Sans 3, sans-serif">Portfolio</text>
  </svg>
  <p class="rtext" style="left:57px;top:17px">Abbildung der gesamten Prozesskette aus einer Hand</p>
  <svg class="ricon" style="left:68px;top:64px"><use href="#i-puzzle"/></svg>
  <div class="band">Gute Gründe / Vorteile</div>
  <div class="strip-label">FILOVAN · 05</div>
</section>

<section class="slide c5 r6 bg-grey">
  <div class="fact-card"></div>
  <svg class="arcs" viewBox="0 0 174 85" aria-hidden="true">
    <g fill="none" stroke-width="2.6">
      <path d="M26 43 A13 13 0 0 1 52 43" stroke="#e4e4e4"/>
      <path d="M52 43 A13 13 0 0 0 78 43" stroke="#e4e4e4"/>
      <path d="M85 43 A17 17 0 0 1 119 43" stroke="#35373a"/>
      <path d="M124 43 A13 13 0 0 0 150 43" stroke="#e4e4e4"/>
    </g>
    <g font-size="1.8" fill="#bbb" text-anchor="middle" font-family="Source Sans 3, sans-serif"><text x="39" y="44">Vertrauen</text><text x="65" y="44">Portfolio</text><text x="137" y="44">Mitarbeiter</text></g>
    <text x="102" y="44" font-size="3" font-weight="600" fill="#333" text-anchor="middle" font-family="Source Sans 3, sans-serif">Erfahrung</text>
  </svg>
  <svg class="ricon" style="left:98px;top:12px"><use href="#i-star"/></svg>
  <p class="rtext" style="left:87px;top:55px">Referenzprojekte in allen Größen und Branchen</p>
  <div class="band">Gute Gründe / Vorteile</div>
  <div class="strip-label">FILOVAN · 05</div>
</section>

<section class="slide c6 r6 bg-grey">
  <div class="fact-card"></div>
  <svg class="arcs" viewBox="0 0 174 85" aria-hidden="true">
    <g fill="none" stroke-width="2.6">
      <path d="M24 43 A13 13 0 0 1 50 43" stroke="#e4e4e4"/>
      <path d="M50 43 A13 13 0 0 0 76 43" stroke="#e4e4e4"/>
      <path d="M76 43 A13 13 0 0 1 102 43" stroke="#e4e4e4"/>
      <path d="M110 43 A17 17 0 0 0 144 43" stroke="#b5b5b5"/>
    </g>
    <g font-size="1.8" fill="#bbb" text-anchor="middle" font-family="Source Sans 3, sans-serif"><text x="37" y="44">Vertrauen</text><text x="63" y="44">Portfolio</text><text x="89" y="44">Erfahrung</text></g>
    <text x="127" y="44" font-size="3" font-weight="600" fill="#333" text-anchor="middle" font-family="Source Sans 3, sans-serif">Mitarbeiter</text>
  </svg>
  <p class="rtext" style="left:112px;top:12px">Alle Leistungen werden durch eigenes Personal ohne Einbindung von Subunternehmern erbracht</p>
  <svg class="ricon" style="left:123px;top:64px"><use href="#i-people"/></svg>
  <div class="band">Gute Gründe / Vorteile</div>
  <div class="strip-label">FILOVAN · 05</div>
</section>

<!-- ROW 7 -->
<section class="slide c1 r7">
  <div class="sec-photo" role="img" aria-label="Company building, faded background"></div>
  <div class="sec-panel inset bg-dark"></div>
  <div class="sec-num" style="left:22px;top:52px">06</div>
  <div class="sec-title" style="left:79px;top:68px">Die 100% Philosophie.</div>
</section>

<section class="slide c2 r7 bg-dark">
  <div class="head">Die 100% Philosophie</div><div class="card"></div>
  <ul class="plist">
    <li><i><svg width="5" height="5"><use href="#i-house"/></svg></i>Das System</li>
    <li><i><svg width="5" height="5"><use href="#i-hands"/></svg></i>Dienstleistungen</li>
    <li><i><svg width="5" height="5"><use href="#i-shield"/></svg></i>Datenschutz &amp; Zertifizierungen</li>
  </ul>
  <div class="foot"><span class="mark sm"><i></i>FILOVAN</span><span>PRESENTATION TITLE<b>06</b></span></div>
</section>

<section class="slide c3 r7 bg-dark">
  <div class="head">Die 100% Philosophie</div><div class="card ph-card"></div>
  <div class="picol"><i class="on"><svg><use href="#i-house"/></svg></i><i><svg><use href="#i-hands"/></svg></i><i><svg><use href="#i-shield"/></svg></i></div>
  <div class="phtitle">Das System</div>
  <svg class="phicon"><use href="#i-house"/></svg>
  <ul class="phbox"><li>100% eigenes Rechenzentrum mit 24x7 Betrieb, inkl. Backup Rechenzentrum</li><li>Zertifizierter KVR Partner</li><li>Echte, vollständig eigenentwickelte SaaS-Lösung nur für den RZ Betrieb</li><li>Wartung, Support und Updates inklusive</li><li>Webbasierte Anwendung</li></ul>
  <div class="foot"><span class="mark sm"><i></i>FILOVAN</span><span>PRESENTATION TITLE<b>06</b></span></div>
</section>

<section class="slide c4 r7 bg-dark">
  <div class="head">Die 100% Philosophie</div><div class="card ph-card"></div>
  <div class="picol"><i><svg><use href="#i-house"/></svg></i><i class="on"><svg><use href="#i-hands"/></svg></i><i><svg><use href="#i-shield"/></svg></i></div>
  <div class="phtitle">Dienstleistungen</div>
  <svg class="phicon"><use href="#i-hands"/></svg>
  <ul class="phbox"><li>Kombination aus Mensch &amp; Maschine</li><li>Service Level Agreements, Dienstleistung zeitlich definiert</li><li>Vertragsstrafe bei Nicht-Erreichung</li></ul>
  <div class="foot"><span class="mark sm"><i></i>FILOVAN</span><span>PRESENTATION TITLE<b>06</b></span></div>
</section>

<section class="slide c5 r7 bg-dark">
  <div class="head">Die 100% Philosophie</div><div class="card ph-card"></div>
  <div class="picol"><i><svg><use href="#i-house"/></svg></i><i><svg><use href="#i-hands"/></svg></i><i class="on"><svg><use href="#i-shield"/></svg></i></div>
  <div class="phtitle">Datenschutz und<br>Zertifizierungen</div>
  <svg class="phicon" style="top:50px"><use href="#i-shield"/></svg>
  <ul class="phbox"><li>Alle gängigen Zertifizierungen</li><li>Eigenes Compliance Management</li><li>Datenschutz gem. DSGVO</li></ul>
  <div class="foot"><span class="mark sm"><i></i>FILOVAN</span><span>PRESENTATION TITLE<b>06</b></span></div>
</section>

<!-- ROW 8 -->
<section class="slide c1 r8" style="background:var(--navy)">
  <div class="photo" role="img" aria-label="Company building, faint dark overlay" style="background:linear-gradient(180deg,#2c3744,#27323e 60%,#222b35)"></div>
  <div class="thx-word" style="left:17px;top:30px">Danke.</div>
  <div class="contact" style="left:16px">
    <span class="mark sm" style="color:#fff;font-size:4px"><i style="width:3px;height:2.4px"></i>FILOVAN</span>
    <span class="vl"></span>
    <p>FILOVAN Information Factory GmbH<br>Lindenweg 12<br>57000 Lindtal</p>
    <span class="vl"></span>
    <p>+49 (0)123 456780<br>kontakt@filovan.de</p>
  </div>
  <div class="social"><i></i><i></i><i></i></div>
  <div class="web">filovan.de</div>
</section>

<section class="slide c2 r8" style="background:var(--navy)">
  <div class="photo light" role="img" aria-label="Company building beside a lake, light toned" style="bottom:42px"></div>
  <div class="thx-word" style="left:16px;top:25px;color:var(--ink)">Danke.</div>
  <div class="contact" style="left:16px;top:76px">
    <span class="mark sm" style="color:#fff;font-size:4px"><i style="width:3px;height:2.4px"></i>FILOVAN</span>
    <span class="vl"></span>
    <p>FILOVAN Information Factory GmbH<br>Lindenweg 12<br>57000 Lindtal</p>
    <span class="vl"></span>
    <p>+49 (0)123 456780<br>kontakt@filovan.de</p>
  </div>
  <div class="social"><i></i><i></i><i></i></div>
  <div class="web">filovan.de</div>
</section>

</body>
</html>
```